Probate (Legal) Wordpress Design with Coding for Online Company

I need a Wordpress design with coding, pictures, content to be provided by me, fully responsive, and development. This is for a 6-7 page design.

Pages Needed: Home/About/Probate/Process/FAQ/Contact Us/Blog.

The home page should be organized as followed:
-Steps in Probate: Gather; Implement; Close (each step will come with content)
-Flat-Fee Price & Savings: Content will go here with a button to contact us (phone number) or just the phone number.
-You Have Questions, We Have Answers: five questions with content. Only one question answer to show at a time when clicked on the question from the list.
-Get to Know Us: a brief description with content about what we do and who we are.

Main image slogan: Helping Californians deal with loss with DIGNITY & UNDERSTATING (you may use a better slogan if you wish).

The Contact page should not have a map since we are an online company. We service the entire state of California in every county and city.

The About page should be simple, direct, and easy on the eye. It should have a brief description of who we are and it should have no more than 6 reasons why the client should hire us.

About our online California company. We are not attorneys but legal document assistants who prepare legal documents for probate estate when someone dies with or without a will and assets need to be distributed. We have a flat-fee for Formal Probate of $999 and $699 for Informal Probate. We are an online company and offer our services to the entire state of California in every county. We do everything over the phone and email. The turn around time for us to prepare the initial legal paperwork for the client is within 3-5 business days. We can prepare, file, serve and manage a probate matter from petition to closing. We are not attorneys so our prices are very affordable compare to the attorney.

The company name for the website will be www.velmarhollow.com, The Velmar Hollow Group.

I do not have a logo yet. The colors of the website should be easy on the eye and calming. THE SITE SHOULD BE SIMPLE AND STRAIGHT TO THE POINT. EASY TO NAVIGATE.

The company phone number should be very visible and should stand out to the client. It should also be clickable and ready to dial for smartphone users.

I do not want a contact form on the homepage. THE MAIN THING IS FOR THE POTENTIAL CLIENT TO CALL OUR OFFICE TO SIGN UP.

I do like some images of family or people since we are dealing with people who just lost a loved one. Not all the images have to be of people.

The site should not look like we practice law or that people can mistake us for attorneys.

Target Market(s)

People who just lost a loved one who had property, assets, in California but died with or without a will or trust. This is for people looking to hire non-attorneys.

Coding

Coded - Design and coding required

Font styles to use
Serif

Colors

Designer to choose colors to be used in the design.

Requirements
Must have
• Refer to Project Description.
Nice to have
• The sample images provided is what I am attracted to for the homepage image.
Should not have

```html
<!DOCTYPE html>
<html lang="en">
<head>
<meta charset="utf-8">
<title>The Velmar Hollow Group — Probate Document Assistance</title>
<link rel="stylesheet" href="https://fonts.googleapis.com/css2?family=Crimson+Text:wght@400;600;700&family=Open+Sans:wght@400;600;700&family=Oswald:wght@500;600&display=swap">
<style>
:root{
  --teal:#14667f;
  --teal-deep:#0f5468;
  --orange:#f47c0b;
  --ink:#333333;
  --muted:#555555;
  --dark:#444444;
  --sky:#edf7fa;
  --white:#ffffff;
  --serif:"Crimson Text", Georgia, serif;
  --sans:"Open Sans", Arial, sans-serif;
  --cond:"Oswald", "Arial Narrow", sans-serif;
}
*{box-sizing:border-box;margin:0;padding:0}
html,body{width:1200px;height:3358px;overflow:hidden}
body{position:relative;background:var(--white);font-family:var(--sans);color:var(--ink)}
.abs{position:absolute}
a{color:inherit;text-decoration:none}

/* header */
.top-line{left:0;top:0;width:1200px;height:4px;background:var(--orange)}
.call-pill{left:795px;top:0;width:302px;height:42px;background:var(--orange);border-radius:0 0 22px 22px;color:var(--white);font-size:16px;font-weight:600;display:flex;align-items:center;justify-content:center;gap:10px}
.brand{left:98px;top:80px;display:flex;align-items:center;gap:10px}
.brand-mark{width:20px;height:20px;background:var(--orange)}
.brand-name{font-family:var(--serif);font-weight:700;font-size:21px;color:var(--teal);letter-spacing:.5px;white-space:nowrap}
.main-nav{left:456px;top:78px;display:flex}
.main-nav a{font-size:15px;font-weight:600;color:#222;margin-right:34px}

/* hero */
.hero{left:0;top:125px;width:1200px;height:518px;background:linear-gradient(100deg,#e7e2d8 0%,#cfc6b8 40%,#8f8473 70%,#6d6253 100%)}
.hero-arrow{top:360px}
.hero-title{left:98px;top:222px;font-family:var(--serif);font-size:44px;font-weight:400;color:var(--white);letter-spacing:1px;padding-bottom:14px;border-bottom:2px solid rgba(255,255,255,.85);line-height:1.1;white-space:nowrap}
.hero-slogan{left:98px;top:336px;font-family:var(--cond);font-weight:600;font-size:26px;line-height:40px;color:var(--teal);text-transform:uppercase;white-space:nowrap}
.btn{display:flex;align-items:center;justify-content:center;background:var(--orange);color:var(--white);font-size:15px;font-weight:600;text-transform:uppercase}
.hero-btn{left:98px;top:448px;width:115px;height:50px;border:2px solid rgba(255,255,255,.85)}

/* about band */
.about-band{left:0;top:643px;width:1200px;height:248px}
.about-title{left:0;top:682px;width:1200px;text-align:center;font-family:var(--serif);font-weight:700;font-size:32px;color:var(--white);letter-spacing:.5px}
.about-text{left:110px;top:754px;width:980px;text-align:center;font-size:13.5px;line-height:22px;font-weight:600;color:var(--white)}

/* section headings */
.sec-title{left:0;width:1200px;text-align:center;font-family:var(--serif);font-weight:700;font-size:33px;color:var(--teal);letter-spacing:.5px}
.sec-rule{left:560px;width:80px;height:2px;background:var(--teal)}

/* how it works */
.step-title{font-family:var(--serif);font-weight:700;font-size:28px}
.step-text{font-size:14px;line-height:22px;color:var(--muted)}
.gather .step-title{color:var(--orange)}
.close .step-title{color:var(--teal)}
.implement .step-title{color:var(--dark)}

/* flat fee */
.fee-band{left:0;top:1612px;width:1200px;height:372px;background:var(--sky)}
.fee-photo{left:0;top:1612px;width:526px;height:372px;background:radial-gradient(ellipse at 50% 55%,#d9778f 0%,#e6b5a8 30%,#f3ece7 62%,var(--sky) 100%)}
.fee-title{left:544px;top:1664px;font-family:var(--serif);font-weight:700;font-size:38px;color:var(--teal)}
.fee-text{left:544px;top:1730px;width:556px;font-size:14px;line-height:25px;color:var(--muted);text-align:justify}
.fee-btn{left:544px;top:1865px;width:217px;height:54px;font-size:14px}

/* faq */
.faq-list{left:98px;top:2177px;width:435px}
.faq-q{position:relative;height:50px;margin-bottom:10.5px;width:404px;border:2px solid var(--teal);border-radius:25px;display:flex;align-items:center;padding-left:22px;font-size:14.5px;color:var(--teal);font-weight:600}
.faq-q.active{background:var(--orange);border-color:var(--orange);color:var(--white);border-radius:25px 0 0 25px}
.faq-q.active::after{content:"";position:absolute;right:-31px;top:-2px;border-left:29px solid var(--orange);border-top:25px solid transparent;border-bottom:25px solid transparent}
.faq-answer{left:549px;top:2196px;width:553px}
.faq-answer h3{font-size:18px;font-weight:700;color:var(--teal);margin-bottom:14px;letter-spacing:.3px}
.faq-answer p{font-size:14px;line-height:23px;color:var(--muted);margin-bottom:24px}
.faq-answer li{list-style:none;display:flex;align-items:center;gap:12px;font-size:13.5px;font-weight:600;color:#222;height:31px}

/* split */
.split{top:2570px;width:600px;height:486px}
.split-do{left:0;background:linear-gradient(120deg,#2b89a8 0%,#15728f 55%,#0f5e77 100%)}
.split-who{left:600px;background:linear-gradient(120deg,#c97b1f 0%,#b86b14 55%,#9a5a12 100%)}
.split-col{top:2626px;width:440px;color:var(--white)}
.split-col h2{font-family:var(--serif);font-weight:400;font-size:34px;letter-spacing:.5px;padding-bottom:14px;position:relative;margin-bottom:36px}
.split-col h2::after{content:"";position:absolute;left:0;bottom:0;width:64px;height:2px;background:var(--white)}
.split-col p{font-size:14px;line-height:22px;font-weight:600;margin-bottom:20px}
.outline-btn{display:inline-flex;align-items:center;justify-content:center;width:115px;height:52px;border:2px solid var(--white);font-size:15px;font-weight:600;margin-top:14px}

/* footer */
.foot-nav{left:0;top:3126px;width:1200px;display:flex;justify-content:center;font-size:15px;color:#222;font-weight:500}
.foot-nav span{margin:0 18px}
.foot-contact{left:0;top:3198px;width:1200px;display:flex;justify-content:center;gap:48px;font-size:20px;color:#222}
.foot-contact div{display:flex;align-items:center;gap:14px}
.foot-rule{left:98px;top:3280px;width:1004px;height:1px;background:#222}
.copyright{left:0;top:3308px;width:1200px;text-align:center;font-size:14px;font-weight:600;color:#222}
</style>
</head>
<body>

<header>
  <div class="abs top-line"></div>
  <a class="abs call-pill" href="tel:+1805550142">
    <svg width="16" height="16" viewBox="0 0 16 16"><rect x="0" y="0" width="16" height="16" rx="3" fill="#fff"/><path d="M5 3.5l1.6 2.2-1 1.1a7 7 0 0 0 3.6 3.6l1.1-1 2.2 1.6-.9 1.6c-3.9-.3-7-3.4-7.3-7.3z" fill="#f47c0b"/></svg>
    Call Us At: +180 555 0142
  </a>
  <div class="abs brand"><span class="brand-mark"></span><span class="brand-name">THE VELMAR HOLLOW GROUP</span></div>
  <nav class="abs main-nav">
    <a href="#">HOME</a><a href="#">ABOUT</a><a href="#">PROBATE</a><a href="#">PROCESS</a><a href="#">FAQ</a><a href="#">CONTACT US</a><a href="#" style="margin-right:0">BLOG</a>
  </nav>
</header>

<section>
  <div class="abs hero" role="img" aria-label="Photo of a mother embracing her two young children in comfort"></div>
  <svg class="abs hero-arrow" style="left:28px" width="24" height="54" viewBox="0 0 24 54"><path d="M20 2L4 27l16 25" fill="none" stroke="rgba(255,255,255,.7)" stroke-width="2"/></svg>
  <svg class="abs hero-arrow" style="left:1148px" width="24" height="54" viewBox="0 0 24 54"><path d="M4 2l16 25L4 52" fill="none" stroke="rgba(255,255,255,.7)" stroke-width="2"/></svg>
  <h1 class="abs hero-title">THE VELMAR HOLLOW GROUP</h1>
  <p class="abs hero-slogan">Helping Californians deal with loss with<br>dignity &amp; understating</p>
  <a class="abs btn hero-btn" href="#">Read More</a>
</section>

<section>
  <svg class="abs about-band" viewBox="0 0 1200 248" width="1200" height="248">
    <path d="M0 0H1200V180L600 248L0 180Z" fill="#14667f"/>
    <path d="M6 6H1194V176L600 242L6 176Z" fill="none" stroke="#ffffff" stroke-width="2"/>
    <path d="M594 220l6 6 6-6M594 228l6 6 6-6" fill="none" stroke="#fff" stroke-width="2"/>
  </svg>
  <h2 class="abs about-title">ABOUT PROBATE</h2>
  <p class="abs about-text">We are not attorneys but legal document assistants who prepare legal documents for probate estate when someone dies with or without a will and assets need to be distributed. We have a flat-fee for Formal Probate of $999 and $699 for Informal Probate. We are an online company and offer our services to the entire state of California in every county.</p>
</section>

<section>
  <h2 class="abs sec-title" style="top:946px">HOW IT WORKS</h2>
  <div class="abs sec-rule" style="top:1011px"></div>

  <svg class="abs" style="left:430px;top:1078px" width="340" height="340" viewBox="0 0 340 340">
    <path d="M30 170A140 140 0 0 1 170 30" fill="none" stroke="#f47c0b" stroke-width="4"/>
    <path d="M170 30A140 140 0 0 1 310 170" fill="none" stroke="#14667f" stroke-width="4"/>
    <path d="M310 170A140 140 0 0 1 30 170" fill="none" stroke="#444" stroke-width="4"/>
    <circle cx="71" cy="71" r="27" fill="#f47c0b"/>
    <text x="71" y="80" text-anchor="middle" font-family="Open Sans, sans-serif" font-size="24" font-weight="600" fill="#fff">1</text>
    <circle cx="269" cy="71" r="27" fill="#14667f"/>
    <text x="269" y="80" text-anchor="middle" font-family="Open Sans, sans-serif" font-size="24" font-weight="600" fill="#fff">3</text>
    <circle cx="170" cy="310" r="27" fill="#444"/>
    <text x="170" y="319" text-anchor="middle" font-family="Open Sans, sans-serif" font-size="24" font-weight="600" fill="#fff">2</text>
  </svg>

  <div class="abs gather" style="left:110px;top:1104px;width:300px;text-align:right">
    <h3 class="step-title">Gather:</h3>
    <p class="step-text" style="margin-top:10px">Duis aute irure dolor in reprehenderit in vo luptate velit esse cillum dolore eu fugiat nulla pariatur.</p>
  </div>
  <div class="abs close" style="left:790px;top:1104px;width:310px">
    <h3 class="step-title">Close:</h3>
    <p class="step-text" style="margin-top:10px">Duis aute irure dolor in reprehenderit in vo luptate velit esse cillum dolore eu fugiat nulla pariatur.</p>
  </div>
  <div class="abs implement" style="left:440px;top:1428px;width:320px;text-align:center">
    <h3 class="step-title">Implement:</h3>
    <p class="step-text" style="margin-top:12px">Duis aute irure dolor in reprehenderit in vo luptate velit esse cillum dolore eu fugiat nulla pariatur.</p>
  </div>
</section>

<section>
  <div class="abs fee-band"></div>
  <div class="abs fee-photo" role="img" aria-label="Photo of two hands cupped protectively around a pink piggy bank"></div>
  <h2 class="abs fee-title">Flat-Fee Price &amp; Savings:</h2>
  <p class="abs fee-text">Nemo enim ipsam voluptatem quia voluptas sit aspernatur aut odit aut fugit, sed quia consequuntur magni dolores eos qui ratione voluptatem sequi nesciunt. Neque porro quisquam est, qui dolorem ipsum quia dolor sit amet, consectetur, adipisci velit, sed quia non numquam.</p>
  <a class="abs btn fee-btn" href="tel:+1805550142">Call Us At: +180 555 0142</a>
</section>

<section>
  <h2 class="abs sec-title" style="top:2043px">OUR FAQ</h2>
  <div class="abs sec-rule" style="top:2106px"></div>
  <div class="abs faq-list">
    <div class="faq-q active">Nemo enim ipsam voluptatem quia voluptas?</div>
    <div class="faq-q">Magni dolores eos qui ratione voluptatem?</div>
    <div class="faq-q">Sed ut perspiciatis unde omnis natus?</div>
    <div class="faq-q">Enim ad minima veniam, quis nostrum?</div>
    <div class="faq-q">Quis autem vel eum iure reprehenderit?</div>
  </div>
  <div class="abs faq-answer">
    <h3>NEMO ENIM IPSAM VOLUPTATEM:</h3>
    <p>Sed ut perspiciatis unde omnis iste natus error sit voluptatem accusantium doloremque laudantium, totam rem aperiam, eaque ipsa quae ab illo inventore veritatis et quasi architecto beatae vitae dicta sunt explicabo.</p>
    <ul>
      <li><svg width="14" height="10" viewBox="0 0 14 10"><path d="M0 5h10M6 1l4 4-4 4" fill="none" stroke="#f47c0b" stroke-width="2"/></svg>Sed ut perspiciatis unde omnis iste natus error sit voluptate.</li>
      <li><svg width="14" height="10" viewBox="0 0 14 10"><path d="M0 5h10M6 1l4 4-4 4" fill="none" stroke="#f47c0b" stroke-width="2"/></svg>Accusantium dolorem que laudantium, totam rem.</li>
      <li><svg width="14" height="10" viewBox="0 0 14 10"><path d="M0 5h10M6 1l4 4-4 4" fill="none" stroke="#f47c0b" stroke-width="2"/></svg>Aperiam, eaque ipsa quae ab illo inventore veritatis.</li>
      <li><svg width="14" height="10" viewBox="0 0 14 10"><path d="M0 5h10M6 1l4 4-4 4" fill="none" stroke="#f47c0b" stroke-width="2"/></svg>Quasi architecto beatae vitae dicta sunt explicabo.</li>
    </ul>
  </div>
</section>

<section>
  <div class="abs split split-do" role="img" aria-label="Teal-tinted photo of a person reviewing paperwork at a desk"></div>
  <div class="abs split split-who" role="img" aria-label="Orange-tinted photo of a hand writing on documents with a pen"></div>
  <div class="abs split-col" style="left:98px">
    <h2>WHAT WE DO</h2>
    <p>Sed ut perspiciatis unde omnis iste natus error sit voluptatem accu santium doloremque laudantium, totam rem aperiam, eaque ipsa quae ab illo inventore veritatis et quasi architecto beatae.</p>
    <p>Nemo enim ipsam voluptatem quia voluptas sit aspernatur aut odit aut fugit, sed quia consequuntur magni dolores eos qui ratione vo luptatem.</p>
    <a class="outline-btn" href="#">READ MORE</a>
  </div>
  <div class="abs split-col" style="left:632px">
    <h2>WHO WE ARE</h2>
    <p>Sed ut perspiciatis unde omnis iste natus error sit voluptatem accu santium doloremque laudantium, totam rem aperiam, eaque ipsa quae ab illo inventore veritatis et quasi architecto beatae.</p>
    <p>Nemo enim ipsam voluptatem quia voluptas sit aspernatur aut odit aut fugit, sed quia consequuntur magni dolores eos qui ratione vo luptatem.</p>
    <a class="outline-btn" href="#">READ MORE</a>
  </div>
</section>

<footer>
  <nav class="abs foot-nav">
    <a href="#">HOME</a><span>|</span><a href="#">ABOUT</a><span>|</span><a href="#">PROBATE</a><span>|</span><a href="#">PROCESS</a><span>|</span><a href="#">FAQ</a><span>|</span><a href="#">CONTACT US</a><span>|</span><a href="#">BLOG</a>
  </nav>
  <div class="abs foot-contact">
    <div>
      <svg width="44" height="44" viewBox="0 0 44 44"><circle cx="22" cy="22" r="20" fill="none" stroke="#222" stroke-width="2"/><path d="M16 13l3 4-2 2a10 10 0 0 0 8 8l2-2 4 3-2 3c-7-.5-13-6.5-13.5-13.5z" fill="#222"/></svg>
      <a href="tel:+1805550142">+180 555 0142</a>
    </div>
    <div>
      <svg width="44" height="44" viewBox="0 0 44 44"><circle cx="22" cy="22" r="20" fill="none" stroke="#222" stroke-width="2"/><rect x="12" y="15" width="20" height="14" rx="1" fill="none" stroke="#222" stroke-width="2"/><path d="M12 16l10 7 10-7" fill="none" stroke="#222" stroke-width="2"/></svg>
      <a href="mailto:info@velmarhollow.com">info@velmarhollow.com</a>
    </div>
  </div>
  <div class="abs foot-rule"></div>
  <p class="abs copyright">Copyrights @ 2017 The Velmar Hollow Group. All Rights Reserved.</p>
</footer>

</body>
</html>
```